Coastline Premier Retreats Business Card Design

Design a business card for Coastline Premier Retreats. Look at the website for colors and reference. Card should have logo, name, title, office number, mobile number, email, URL and a tagline like, "Luxury Hotel & Resort Email Marketing" (This might change).

https://www.coastlinepremierretreats.example

The rest I will leave up to your imagination.

Contact Information for Business Card

Logo, name, title, office number, mobile number, email, URL and a tagline like, "Luxury Hotel & Resort Email Marketing" (This might change).

```html
<!DOCTYPE html>
<html lang="en">
<head>
<meta charset="utf-8">
<title>Coastline Premier Retreats — Business Card</title>
<link rel="stylesheet" href="https://fonts.googleapis.com/css2?family=Arimo:wght@400;700&family=Montserrat:wght@400&display=swap">
<style>
  :root {
    --stage: #141414;
    --card-light: #f4f4f3;
    --card-dark: #1a1a1a;
    --accent: #e46f1a;
    --ink: #222222;
    --text: #3a3a3a;
    --white: #f5f5f5;
  }
  * { margin: 0; padding: 0; box-sizing: border-box; }
  html, body { width: 1200px; height: 1059px; overflow: hidden; background: var(--stage); }
  body { position: relative; font-family: "Arimo", Arial, sans-serif; color: var(--text); }

  .card { position: absolute; }
  .card-front { left: 256px; top: 89px; width: 688px; height: 391px; background: var(--card-light); }
  .card-back { left: 253px; top: 547px; width: 694px; height: 394px; background: var(--card-dark); }

  .frame { position: absolute; left: 23px; top: 22px; right: 22px; bottom: 33px;
    border: 2px solid var(--accent); border-bottom: none; }
  .frame-base { position: absolute; bottom: 32px; height: 2px; background: var(--accent); }
  .frame-base.left { left: 23px; width: 155px; }
  .frame-base.right { right: 22px; width: 155px; }

  .brand { position: absolute; left: 0; right: 0; display: flex; justify-content: center; align-items: center; gap: 10px;
    font-family: "Arimo", Arial, sans-serif; font-weight: 700; text-transform: uppercase; letter-spacing: 1px; }
  .brand-mark { width: 14px; height: 14px; background: var(--accent); flex: none; }
  .card-front .brand { top: 86px; font-size: 27px; color: var(--ink); }
  .card-back .brand { top: 175px; font-size: 33px; color: var(--white); }
  .card-back .brand-mark { width: 18px; height: 18px; }

  .identity { position: absolute; right: 392px; top: 200px; text-align: right; }
  .person-name { font-weight: 700; font-size: 29px; color: var(--accent); line-height: 1; letter-spacing: 0.3px; white-space: nowrap; }
  .person-title { font-family: "Montserrat", Arial, sans-serif; font-size: 16px; color: var(--text); margin-top: 5px; }
  .address { font-size: 16px; line-height: 21px; margin-top: 9px; white-space: nowrap; }

  .divider { position: absolute; left: 319px; top: 203px; width: 1.5px; height: 88px; background: var(--accent); }

  .contacts { position: absolute; left: 340px; top: 200px; width: 310px; list-style: none; }
  .contacts li { display: flex; align-items: center; height: 25px; font-size: 15px; white-space: nowrap; }
  .contacts svg { width: 13px; height: 13px; margin-right: 8px; flex: none; fill: var(--accent); }

  .tagline { position: absolute; left: 0; right: 0; top: 345px; text-align: center; font-size: 17px; color: var(--text); }
</style>
</head>
<body>
  <section class="card card-front" aria-label="Business card front">
    <div class="frame"></div>
    <div class="frame-base left"></div>
    <div class="frame-base right"></div>

    <div class="brand"><span class="brand-mark"></span>Coastline Premier Retreats</div>

    <div class="identity">
      <h1 class="person-name">DANIEL REYES</h1>
      <p class="person-title">CEO/Founder</p>
      <p class="address">Po Box, 48 Harbor Ln<br>Bayview, AB 10420</p>
    </div>

    <div class="divider"></div>

    <ul class="contacts">
      <li><svg viewBox="0 0 16 16" aria-hidden="true"><path d="M4 1h8a1 1 0 0 1 1 1v12a1 1 0 0 1-1 1H4a1 1 0 0 1-1-1V2a1 1 0 0 1 1-1zm.5 1.5v9h7v-9zM8 12.5a.8.8 0 1 0 0 1.6.8.8 0 0 0 0-1.6z"/></svg>555.214.7300</li>
      <li><svg viewBox="0 0 16 16" aria-hidden="true"><path d="M1 6c0-2 3-3.5 7-3.5S15 4 15 6v1.2h-3.2V5.6H4.2v1.6H1zM4 8h8l2 5H2zm4 1.3a1.6 1.6 0 1 0 0 3.2 1.6 1.6 0 0 0 0-3.2z"/></svg>+34 600 123 457</li>
      <li><svg viewBox="0 0 16 16" aria-hidden="true"><path d="M1 6l7-5 7 5v8H1zm1.6.6L8 10.3l5.4-3.7L8 2.8z"/></svg>info@coastlinepremierretreats.example</li>
      <li><svg viewBox="0 0 16 16" aria-hidden="true"><path d="M8 1a7 7 0 1 0 0 14A7 7 0 0 0 8 1zm-1 2.2c-.6 1-2 1.3-2 2.8 0 1 1.3 1 1.8 2 .4.9-.5 1.8.2 3 .4.6.3 1.3.2 1.8A5.6 5.6 0 0 1 2.5 7.2 5.6 5.6 0 0 1 7 3.2zm3 .3a5.6 5.6 0 0 1 3.3 7c-.6-.3-1.3-1.2-2-1.2-.8 0-1.2-1.1-2.3-1.1-.8 0-1-.9-.4-1.5.7-.7 1.6-.3 1.8-1.2.2-.8-.6-1.2-.4-2z"/></svg>www.coastlinepremierretreats.example</li>
    </ul>

    <p class="tagline">Luxury Hotel &amp; Resort Email Marketing</p>
  </section>

  <section class="card card-back" aria-label="Business card back">
    <div class="brand"><span class="brand-mark"></span>Coastline Premier Retreats</div>
  </section>
</body>
</html>
```